Summer Music/Chorus/Choir Camp for Young Singers Ages 8-13

We need a flyer for a summer camp for young singers ages 8-13. We are nonprofit community children's chorus in Miami, FL. Our camp provides specialized training in music theory, sight-reading,and aural training through daily choral rehearsals in an environment that is both positive and a lot of fun! Our camp offers children the opportunity to come as they are, no matter the level of experience, and grow tremendously in their musicianship skills. In addition to this, our campers participate in song-writing, masterclasses, community performances, and media projects. The final design should be clean, fun, not too crowded, should appeal to boys and girls ages 8-13, and something someone that age would consider "cool" and not too childish. Drawings are cool, something different.
Updates

Target Market(s)

Ages 8-13 and parents of those kids.

Industry/Entity Type

Community

Requirements
Must have
• All info attached.
Nice to have
• Things that relate to music, especially related to singing/choirs
Should not have
• instruments, stock photos of children, or photos from our website (unless they are used very creatively), or photos in general. I've attached our previous camp flyer and our current organization flyer but I don't necessarily want this flyer to look like those.

```html
<!DOCTYPE html>
<html lang="en">
<head>
<meta charset="utf-8">
<title>Summer Camp for Young Singers</title>
<link rel="stylesheet" href="https://fonts.googleapis.com/css2?family=Oswald:wght@400;500;600&family=Sniglet:wght@400&family=Roboto:wght@400&display=swap">
<style>
  :root {
    --page-bg: #b9b7b3;
    --paper: #ffffff;
    --ink-light: #ffffff;
    --ink-shadow: rgba(20, 20, 40, 0.85);
    --navy: #1d2445;
    --gold: #e8b34a;
    --orange: #f28a2e;
    --teal: #2f8fb5;
    --blue: #3a63a8;
    --magenta: #e0307a;
    --violet: #7a3fa0;
    --yellow: #f6d45a;
    --badge: #2b2b2b;
    --fine-print: #555555;
  }
  * { box-sizing: border-box; margin: 0; padding: 0; }
  html, body { width: 1178px; height: 1200px; overflow: hidden; }
  body { background: var(--page-bg); position: relative; font-family: "Oswald", sans-serif; }

  .flyer {
    position: absolute; left: 248px; top: 105px;
    width: 657px; height: 877px;
    background: var(--paper);
    box-shadow: 0 4px 10px rgba(0,0,0,0.25);
    overflow: hidden;
  }
  .flyer__art {
    position: absolute; left: 12px; top: 12px; width: 633px; height: 805px;
    background:
      radial-gradient(ellipse at 80% 45%, rgba(58,99,168,0.9), transparent 55%),
      radial-gradient(ellipse at 15% 45%, rgba(242,138,46,0.9), transparent 50%),
      radial-gradient(ellipse at 25% 75%, rgba(224,48,122,0.95), transparent 50%),
      radial-gradient(ellipse at 85% 80%, rgba(246,212,90,0.9), transparent 45%),
      radial-gradient(ellipse at 50% 20%, rgba(47,143,181,0.6), transparent 55%),
      linear-gradient(180deg, var(--navy) 0%, #3b3f6a 12%, var(--gold) 25%, var(--teal) 45%, var(--violet) 62%, var(--magenta) 80%, var(--yellow) 100%);
  }
  .flyer__kids {
    position: absolute; left: 12px; top: 545px; width: 633px; height: 272px;
    background: linear-gradient(180deg, rgba(255,255,255,0) 0%, rgba(255,255,255,0.55) 45%, #ffffff 100%);
  }

  .shadow-text { color: var(--ink-light); text-shadow: 2px 2px 3px var(--ink-shadow); }

  .brand {
    position: absolute; left: 24px; top: 40px; width: 320px;
    font-weight: 500; font-size: 36px; line-height: 40px;
    color: var(--ink-light);
  }
  .invite {
    position: absolute; right: 32px; top: 44px; text-align: right;
    font-weight: 500; font-size: 30px; line-height: 35px;
  }
  .headline {
    position: absolute; left: 24px; right: 24px; top: 204px; text-align: center;
    font-family: "Sniglet", sans-serif; font-weight: 400;
    font-size: 62px; line-height: 68px; white-space: nowrap;
    -webkit-text-stroke: 1px #222;
  }
  .cost {
    position: absolute; left: 0; right: 0; top: 386px; text-align: center;
    font-weight: 500; font-size: 30px; line-height: 36px;
  }
  .schedule {
    position: absolute; left: 0; right: 0; top: 480px; text-align: center;
    font-weight: 500; font-size: 15px; line-height: 28px;
  }
  .contact {
    position: absolute; left: 0; right: 0; top: 676px; text-align: center;
    font-weight: 500; font-size: 27px; line-height: 35px;
  }
  .partners { position: absolute; left: 0; top: 0; }
  .partner { position: absolute; background: var(--badge); }
  .partner--square { left: 45px; top: 793px; width: 48px; height: 48px; }
  .partner--rect { left: 276px; top: 793px; width: 100px; height: 44px; border-radius: 2px; }
  .partner--bar { left: 449px; top: 810px; width: 172px; height: 20px; }
  .fine-print {
    position: absolute; left: 16px; top: 855px;
    font-family: "Roboto", sans-serif; font-size: 9px; color: var(--fine-print);
  }
</style>
</head>
<body>
  <main class="flyer">
    <div class="flyer__art" role="img" aria-label="Colourful watercolour background with faint music notes and staff lines"></div>
    <div class="flyer__kids" role="img" aria-label="White silhouettes of children jumping and dancing on grass"></div>

    <div class="brand">Bright Harmony<br>Youth Chorus</div>

    <p class="invite shadow-text">Singers in grades<br>3-9 are invited<br>to attend!</p>

    <h1 class="headline shadow-text">Summer camp for<br>young singers</h1>

    <p class="cost shadow-text">Cost- &nbsp;*$300 for 2-week session<br>*Price does not include lunch.</p>

    <p class="schedule shadow-text">Dates and Times- July 18-29, 9am-3pm (M-F)*.<br>*Extended hours available (7:30am-5:30pm) for an extra $50 per week.</p>

    <p class="contact shadow-text">Phone- 555.014.2380<br>Email- hello@brightharmonychorus.org</p>

    <div class="partners" aria-label="Partner badges">
      <div class="partner partner--square"></div>
      <div class="partner partner--rect"></div>
      <div class="partner partner--bar"></div>
    </div>

    <p class="fine-print">Bright Harmony is a 501 (c)(3) Nonprofit organization. Donations made to BHYC are tax-exempt.</p>
  </main>
</body>
</html>
```